Website for vegan focused blog

A website is needed so that I can launch my new blog in Dubai. It will be mainly vegan focused but also lifestyle based. Wordpress based- i started to build a site on Wordpress but design is not my forte ;)
Main content on the site will be; my recipes, reviews of products/restaurants, lifestyle posts and travel.
For this I ask for a homepage design, a recipe design page that includes a recipe card and a generic page for posts that can show pictures and videos. Also a contact me page.
Main headers should be: Home, Recipes and happy for suggestions.
Must look clean and neat but appealing, happy for minimalist look. I like pink and grey colours. Must be Wordpress compatible.
Have attached a couple of example posts for reference
Must have social links etc.
name of blog is: Maren by the dunes
Other blogs I like are: https://quietladleoven.com/ https://wellfernkitchen.com/ https://wellfernkitchen.com/ https://www.ohladycakes.com/https://beetsatsupper.com/ https://dorintalve.com/

Target Market(s)

Residents in the UAE. General individuals interested in vegan meals, plant based nutrition, travel and reviews.

Number of Pages Required

4 page

Colors
eea4c8
eda3c7
f9d9e8
dbdbdb
aaaaaa
d5d5d5

Requirements
Must have
• Recipe page- must include recipe card plug in option
• Social media integration
• Email sign ups

```html
<!DOCTYPE html>
<html lang="en">
<head>
<meta charset="utf-8">
<title>Maren by the dunes — Vegan Food</title>
<link href="https://fonts.googleapis.com/css2?family=Oswald:wght@400;500;600&family=Open+Sans:wght@400;600;700&display=swap" rel="stylesheet">
<style>
:root{
  --pink:#e0619f;
  --pink-soft:#eea4c8;
  --pink-pale:#f9d9e8;
  --grey-line:#dbdbdb;
  --grey-mid:#aaaaaa;
  --grey-box:#d5d5d5;
  --ink:#222;
  --text:#555;
  --footer:#0b0b0b;
  --white:#fff;
}
*{box-sizing:border-box;margin:0;padding:0}
html,body{width:1200px;height:3536px;overflow:hidden;background:var(--white)}
body{position:relative;font-family:"Open Sans",Arial,sans-serif;color:var(--text)}
.abs{position:absolute}

/* header */
.site-header{left:0;top:0;width:1200px;height:112px;border-top:6px solid var(--pink)}
.brand{left:80px;top:38px;font-family:"Open Sans",Arial,sans-serif;font-weight:700;font-size:26px;color:var(--pink)}
.main-nav{right:80px;top:40px;display:flex;gap:34px;align-items:center;font-size:16px;color:var(--ink)}
.main-nav .active{color:var(--pink)}
.lang{border:1px solid var(--grey-box);border-radius:16px;padding:5px 14px;font-size:14px;display:flex;gap:8px;align-items:center}

/* hero */
.hero{left:0;top:112px;width:1200px;height:568px;background:linear-gradient(100deg,#c9b7a5 0%,#e7e1d5 30%,#b9c79a 55%,#6f8f4c 80%,#3e5a2c 100%)}
.hero-text{left:590px;top:300px;color:var(--white);font-family:"Oswald",Arial,sans-serif;font-weight:600;text-transform:uppercase;line-height:1.05}
.hero-text .kicker{font-size:46px;letter-spacing:1px}
.hero-text .title{font-size:78px;letter-spacing:3px;word-spacing:18px}
.hero-dots{left:1070px;top:612px;display:flex;gap:8px}
.hero-dots span{width:18px;height:18px;border-radius:50%;background:rgba(255,255,255,.55)}
.hero-dots span:first-child{background:var(--white)}

/* about */
.about-photo{left:590px;top:792px;width:520px;height:320px;background:linear-gradient(180deg,#f0a86b 0%,#c7825a 40%,#4d5563 70%,#2b2f36 100%);z-index:1}
.about-card{left:90px;top:768px;width:580px;height:368px;border:2px solid var(--grey-box);background:var(--white);padding:44px 40px;z-index:2}
.about-card h2{font-weight:400;font-size:34px;color:var(--ink);margin-bottom:18px}
.about-card p{font-size:13px;line-height:1.75;width:330px}
.btn{display:inline-block;background:var(--pink);color:var(--white);font-size:12px;padding:6px 16px;border-radius:2px}
.about-card .btn{margin-top:18px}

/* sections */
.section-title{font-family:"Oswald",Arial,sans-serif;font-size:30px;font-weight:500;color:var(--ink);text-transform:uppercase}

/* recipe cards */
.recipe-card{left:88px;width:692px;height:272px;border:1px solid var(--grey-box);border-top:3px solid var(--pink-soft);background:var(--white);box-shadow:0 2px 6px rgba(0,0,0,.08)}
.recipe-card .thumb{position:absolute;left:16px;top:16px;width:240px;height:238px}
.recipe-card .body{position:absolute;left:280px;top:18px;width:390px}
.recipe-card h3{font-size:17px;font-weight:600;color:var(--ink);margin-bottom:8px}
.meta{font-size:12px;color:var(--pink);margin-bottom:8px}
.recipe-card p{font-size:12.5px;line-height:1.6;margin-bottom:14px}

/* sidebar */
.sidebar-box{left:808px;width:304px;border:1px solid var(--grey-box);border-top:3px solid var(--pink-soft);background:var(--white);box-shadow:0 2px 6px rgba(0,0,0,.06)}
.post-item{display:flex;gap:12px;padding:12px 14px 0;height:92px}
.post-item .thumb{width:64px;height:64px;flex:none}
.post-item p{font-size:13px;line-height:1.45;color:var(--ink)}
.post-icons{display:flex;gap:12px;margin-top:6px}
.post-icons svg{width:12px;height:12px}
.view-more{display:block;text-align:center;font-size:13px;color:var(--pink);padding:18px 0 22px}
.tags{display:flex;flex-wrap:wrap;gap:12px;padding:22px 18px}
.tag{background:#2c2c2c;color:var(--white);font-size:12px;padding:6px 14px}
.tag.hot{background:var(--pink)}
.social-tile{width:96px;height:132px;color:var(--white);text-align:center;font-size:11px;padding-top:30px}
.social-tile .dot{width:30px;height:30px;border-radius:50%;background:rgba(255,255,255,.9);margin:0 auto 14px}

/* pagination */
.pagination{left:88px;top:3196px;display:flex;gap:6px}
.pagination span{border:1px solid var(--grey-box);font-size:11px;padding:4px 9px;color:var(--text)}
.pagination .current{background:var(--pink);border-color:var(--pink);color:var(--white)}

/* footer */
.site-footer{left:0;top:3236px;width:1200px;height:300px;background:var(--footer);border-top:10px solid var(--pink);text-align:center;color:#ccc}
.site-footer .brand-foot{font-family:"Open Sans",Arial,sans-serif;font-weight:700;font-size:26px;color:var(--white);margin-top:64px}
.foot-social{display:flex;justify-content:center;gap:22px;margin:34px 0 26px}
.foot-social span{width:42px;height:42px;border-radius:50%;background:#2a2a2a;border:1px solid #444}
.foot-social span.on{background:var(--pink);border-color:var(--pink)}
.site-footer small{font-size:14px}
</style>
</head>
<body>

<header class="site-header abs">
  <div class="brand abs">Maren by the dunes</div>
  <nav class="main-nav abs">
    <span class="active">Home</span><span>Recipe</span><span>Blog</span><span>Contact</span>
    <span class="lang">English <svg width="10" height="6" viewBox="0 0 10 6"><path d="M1 1l4 4 4-4" stroke="#555" fill="none" stroke-width="1.5"/></svg></span>
  </nav>
</header>

<section class="hero abs" role="img" aria-label="Woman eating a fresh green salad at a table with vegetables"></section>
<div class="hero-text abs"><div class="kicker">Maren by the dunes</div><div class="title">Vegan Food</div></div>
<div class="hero-dots abs"><span></span><span></span></div>

<div class="about-photo abs" role="img" aria-label="Person walking along a beach at sunset"></div>
<section class="about-card abs">
  <h2>About Me</h2>
  <p>I'm Maren, born and raised in a small seaside town and now living in Dubai, where I've been cooking plant based food since 2012. I love cooking for friends, trying new cafés, travelling, and hiking the dunes. Join me for simple recipes, honest reviews and tips that fit an easy, healthy everyday life.</p>
  <span class="btn">Read More</span>
</section>

<h2 class="section-title abs" style="left:88px;top:1376px">Recipe</h2>
<h2 class="section-title abs" style="left:808px;top:1376px">Blog Post</h2>

<article class="recipe-card abs" style="top:1436px"><div class="thumb" role="img" aria-label="Roasted vegetable dish" style="background:linear-gradient(135deg,#c98a43,#7b4a22)"></div><div class="body"><h3>Neque porro quisquam est qui dolorem ipsum</h3><div class="meta">September 3, 2018 &nbsp;·&nbsp; 3 Comments</div><p>It is a long established fact that a reader will be distracted by the readable content of a page when looking at its layout. The point of using Lorem Ipsum is that it has a more-or-less normal distribution of letters, as opposed to using 'Content here, content here', making it look like readable.</p><span class="btn">Read More</span></div></article>
<article class="recipe-card abs" style="top:1728px"><div class="thumb" role="img" aria-label="Vegan tacos with salsa" style="background:linear-gradient(135deg,#d9b47a,#8a5a2e)"></div><div class="body"><h3>Porro quisquam est qui dolorem ipsum dolor</h3><div class="meta">September 3, 2018 &nbsp;·&nbsp; 3 Comments</div><p>It is a long established fact that a reader will be distracted by the readable content of a page when looking at its layout. The point of using Lorem Ipsum is that it has a more-or-less normal distribution of letters, as opposed to using 'Content here, content here', making it look like readable.</p><span class="btn">Read More</span></div></article>
<article class="recipe-card abs" style="top:2020px"><div class="thumb" role="img" aria-label="Green smoothies in glasses" style="background:linear-gradient(135deg,#9cc070,#3f6b2a)"></div><div class="body"><h3>Quisquam est qui dolorem ipsum quia dolor</h3><div class="meta">September 3, 2018 &nbsp;·&nbsp; 3 Comments</div><p>It is a long established fact that a reader will be distracted by the readable content of a page when looking at its layout. The point of using Lorem Ipsum is that it has a more-or-less normal distribution of letters, as opposed to using 'Content here, content here', making it look like readable.</p><span class="btn">Read More</span></div></article>
<article class="recipe-card abs" style="top:2312px"><div class="thumb" role="img" aria-label="Colourful salad bowl" style="background:linear-gradient(135deg,#d0534a,#6e8a3a)"></div><div class="body"><h3>Neque porro quisquam est qui dolorem ipsum</h3><div class="meta">September 3, 2018 &nbsp;·&nbsp; 3 Comments</div><p>It is a long established fact that a reader will be distracted by the readable content of a page when looking at its layout. The point of using Lorem Ipsum is that it has a more-or-less normal distribution of letters, as opposed to using 'Content here, content here', making it look like readable.</p><span class="btn">Read More</span></div></article>
<article class="recipe-card abs" style="top:2604px"><div class="thumb" role="img" aria-label="Plant based burger" style="background:linear-gradient(135deg,#5a3a24,#b57a3a)"></div><div class="body"><h3>Quisquam est qui dolorem ipsum quia dolor</h3><div class="meta">September 3, 2018 &nbsp;·&nbsp; 3 Comments</div><p>It is a long established fact that a reader will be distracted by the readable content of a page when looking at its layout. The point of using Lorem Ipsum is that it has a more-or-less normal distribution of letters, as opposed to using 'Content here, content here', making it look like readable.</p><span class="btn">Read More</span></div></article>
<article class="recipe-card abs" style="top:2896px"><div class="thumb" role="img" aria-label="Berry parfaits in jars" style="background:linear-gradient(135deg,#f0e6e0,#c2404f)"></div><div class="body"><h3>Neque porro quisquam est qui dolorem ipsum</h3><div class="meta">September 3, 2018 &nbsp;·&nbsp; 3 Comments</div><p>It is a long established fact that a reader will be distracted by the readable content of a page when looking at its layout. The point of using Lorem Ipsum is that it has a more-or-less normal distribution of letters, as opposed to using 'Content here, content here', making it look like readable.</p><span class="btn">Read More</span></div></article>

<div class="pagination abs"><span>Prev</span><span class="current">1</span><span>2</span><span>3</span><span>4</span><span>5</span><span>…</span><span>10</span><span>Next</span></div>

<aside class="sidebar-box abs" style="top:1436px">
  <div class="post-item"><div class="thumb" role="img" aria-label="Food photo" style="background:#b98a4e"></div><div><p>Ipsum is simply dummy text of the printing and type</p><div class="post-icons"><svg viewBox="0 0 12 12"><circle cx="6" cy="6" r="5" fill="none" stroke="#aaa"/></svg><svg viewBox="0 0 12 12"><path d="M1 2h10v6H5l-3 3V8H1z" fill="none" stroke="#aaa"/></svg><svg viewBox="0 0 12 12"><path d="M6 10L1.5 5.5a2.5 2.5 0 014.5-2 2.5 2.5 0 014.5 2z" fill="none" stroke="#aaa"/></svg></div></div></div>
  <div class="post-item"><div class="thumb" role="img" aria-label="Food photo" style="background:#c25a3c"></div><div><p>Ipsum is simply dummy text of the printing and type</p><div class="post-icons"><svg viewBox="0 0 12 12"><circle cx="6" cy="6" r="5" fill="none" stroke="#aaa"/></svg><svg viewBox="0 0 12 12"><path d="M1 2h10v6H5l-3 3V8H1z" fill="none" stroke="#aaa"/></svg><svg viewBox="0 0 12 12"><path d="M6 10L1.5 5.5a2.5 2.5 0 014.5-2 2.5 2.5 0 014.5 2z" fill="none" stroke="#aaa"/></svg></div></div></div>
  <div class="post-item"><div class="thumb" role="img" aria-label="Food photo" style="background:#7a9a48"></div><div><p>Ipsum is simply dummy text of the printing and type</p><div class="post-icons"><svg viewBox="0 0 12 12"><circle cx="6" cy="6" r="5" fill="none" stroke="#aaa"/></svg><svg viewBox="0 0 12 12"><path d="M1 2h10v6H5l-3 3V8H1z" fill="none" stroke="#aaa"/></svg><svg viewBox="0 0 12 12"><path d="M6 10L1.5 5.5a2.5 2.5 0 014.5-2 2.5 2.5 0 014.5 2z" fill="none" stroke="#aaa"/></svg></div></div></div>
  <div class="post-item"><div class="thumb" role="img" aria-label="Food photo" style="background:#d49a52"></div><div><p>Ipsum is simply dummy text of the printing and type</p><div class="post-icons"><svg viewBox="0 0 12 12"><circle cx="6" cy="6" r="5" fill="none" stroke="#aaa"/></svg><svg viewBox="0 0 12 12"><path d="M1 2h10v6H5l-3 3V8H1z" fill="none" stroke="#aaa"/></svg><svg viewBox="0 0 12 12"><path d="M6 10L1.5 5.5a2.5 2.5 0 014.5-2 2.5 2.5 0 014.5 2z" fill="none" stroke="#aaa"/></svg></div></div></div>
  <div class="post-item"><div class="thumb" role="img" aria-label="Food photo" style="background:#a8423a"></div><div><p>Ipsum is simply dummy text of the printing and type</p><div class="post-icons"><svg viewBox="0 0 12 12"><circle cx="6" cy="6" r="5" fill="none" stroke="#aaa"/></svg><svg viewBox="0 0 12 12"><path d="M1 2h10v6H5l-3 3V8H1z" fill="none" stroke="#aaa"/></svg><svg viewBox="0 0 12 12"><path d="M6 10L1.5 5.5a2.5 2.5 0 014.5-2 2.5 2.5 0 014.5 2z" fill="none" stroke="#aaa"/></svg></div></div></div>
  <div class="post-item"><div class="thumb" role="img" aria-label="Food photo" style="background:#5e7d3a"></div><div><p>Ipsum is simply dummy text of the printing and type</p><div class="post-icons"><svg viewBox="0 0 12 12"><circle cx="6" cy="6" r="5" fill="none" stroke="#aaa"/></svg><svg viewBox="0 0 12 12"><path d="M1 2h10v6H5l-3 3V8H1z" fill="none" stroke="#aaa"/></svg><svg viewBox="0 0 12 12"><path d="M6 10L1.5 5.5a2.5 2.5 0 014.5-2 2.5 2.5 0 014.5 2z" fill="none" stroke="#aaa"/></svg></div></div></div>
  <div class="post-item"><div class="thumb" role="img" aria-label="Food photo" style="background:#c9884a"></div><div><p>Ipsum is simply dummy text of the printing and type</p><div class="post-icons"><svg viewBox="0 0 12 12"><circle cx="6" cy="6" r="5" fill="none" stroke="#aaa"/></svg><svg viewBox="0 0 12 12"><path d="M1 2h10v6H5l-3 3V8H1z" fill="none" stroke="#aaa"/></svg><svg viewBox="0 0 12 12"><path d="M6 10L1.5 5.5a2.5 2.5 0 014.5-2 2.5 2.5 0 014.5 2z" fill="none" stroke="#aaa"/></svg></div></div></div>
  <div class="post-item"><div class="thumb" role="img" aria-label="Food photo" style="background:#8c5a34"></div><div><p>Ipsum is simply dummy text of the printing and type</p><div class="post-icons"><svg viewBox="0 0 12 12"><circle cx="6" cy="6" r="5" fill="none" stroke="#aaa"/></svg><svg viewBox="0 0 12 12"><path d="M1 2h10v6H5l-3 3V8H1z" fill="none" stroke="#aaa"/></svg><svg viewBox="0 0 12 12"><path d="M6 10L1.5 5.5a2.5 2.5 0 014.5-2 2.5 2.5 0 014.5 2z" fill="none" stroke="#aaa"/></svg></div></div></div>
  <div class="post-item"><div class="thumb" role="img" aria-label="Food photo" style="background:#b34c46"></div><div><p>Ipsum is simply dummy text of the printing and type</p><div class="post-icons"><svg viewBox="0 0 12 12"><circle cx="6" cy="6" r="5" fill="none" stroke="#aaa"/></svg><svg viewBox="0 0 12 12"><path d="M1 2h10v6H5l-3 3V8H1z" fill="none" stroke="#aaa"/></svg><svg viewBox="0 0 12 12"><path d="M6 10L1.5 5.5a2.5 2.5 0 014.5-2 2.5 2.5 0 014.5 2z" fill="none" stroke="#aaa"/></svg></div></div></div>
  <div class="post-item"><div class="thumb" role="img" aria-label="Food photo" style="background:#6d8e45"></div><div><p>Ipsum is simply dummy text of the printing and type</p><div class="post-icons"><svg viewBox="0 0 12 12"><circle cx="6" cy="6" r="5" fill="none" stroke="#aaa"/></svg><svg viewBox="0 0 12 12"><path d="M1 2h10v6H5l-3 3V8H1z" fill="none" stroke="#aaa"/></svg><svg viewBox="0 0 12 12"><path d="M6 10L1.5 5.5a2.5 2.5 0 014.5-2 2.5 2.5 0 014.5 2z" fill="none" stroke="#aaa"/></svg></div></div></div>
  <div class="post-item"><div class="thumb" role="img" aria-label="Food photo" style="background:#d7a25e"></div><div><p>Ipsum is simply dummy text of the printing and type</p><div class="post-icons"><svg viewBox="0 0 12 12"><circle cx="6" cy="6" r="5" fill="none" stroke="#aaa"/></svg><svg viewBox="0 0 12 12"><path d="M1 2h10v6H5l-3 3V8H1z" fill="none" stroke="#aaa"/></svg><svg viewBox="0 0 12 12"><path d="M6 10L1.5 5.5a2.5 2.5 0 014.5-2 2.5 2.5 0 014.5 2z" fill="none" stroke="#aaa"/></svg></div></div></div>
  <div class="post-item"><div class="thumb" role="img" aria-label="Food photo" style="background:#9a4436"></div><div><p>Ipsum is simply dummy text of the printing and type</p><div class="post-icons"><svg viewBox="0 0 12 12"><circle cx="6" cy="6" r="5" fill="none" stroke="#aaa"/></svg><svg viewBox="0 0 12 12"><path d="M1 2h10v6H5l-3 3V8H1z" fill="none" stroke="#aaa"/></svg><svg viewBox="0 0 12 12"><path d="M6 10L1.5 5.5a2.5 2.5 0 014.5-2 2.5 2.5 0 014.5 2z" fill="none" stroke="#aaa"/></svg></div></div></div>
  <span class="view-more">View More »</span>
</aside>

<h2 class="section-title abs" style="left:808px;top:2656px">Tags</h2>
<aside class="sidebar-box abs" style="top:2706px">
  <div class="tags"><span class="tag">Unknown</span><span class="tag">Blog</span><span class="tag">Quisquam</span><span class="tag">Latest News</span><span class="tag">Unknown</span><span class="tag">Neque porro</span><span class="tag hot">Recipes</span><span class="tag">Site plugins</span><span class="tag">Beginners tutorials</span></div>
</aside>

<div class="social-tile abs" style="left:808px;top:2940px;background:#2f4a86"><div class="dot"></div>2,356<br>Fans</div>
<div class="social-tile abs" style="left:912px;top:2940px;background:#2aa6dc"><div class="dot"></div>1,240<br>Followers</div>
<div class="social-tile abs" style="left:1016px;top:2940px;background:#e8712b"><div class="dot"></div>620<br>Subscribers</div>

<footer class="site-footer abs">
  <div class="brand-foot">Maren by the dunes</div>
  <div class="foot-social"><span></span><span class="on"></span><span></span><span></span></div>
  <small>© 2018 Company Name. All rights reserved</small>
</footer>

</body>
</html>
```